We are a recruitment company based in Norwich/Cambridge England.
I have included our company logo which we want to remain the same.

What we are looking for is a new creative Business card which will really stand out!!

Contact Information for Business Card

Harriet Dunmore
email: Harriet@plavex.co.uk
Address: Brackwell House
Fenmoor Enterprise Park
Partridge Way
Norwich
QB9 3KX
Tel:01632 960418

```html
<!DOCTYPE html>
<html lang="en">
<head>
<meta charset="utf-8">
<title>Plavex Business Card</title>
<link href="https://fonts.googleapis.com/css2?family=Montserrat:wght@500;700&family=Arimo:wght@400;700&display=swap" rel="stylesheet">
<style>
  :root {
    --green: #8cc542;
    --grey: #8a878c;
    --white: #ffffff;
    --stage: #2a2a2a;
    --ink-grey: #7d7a80;
  }
  * { box-sizing: border-box; margin: 0; padding: 0; }
  html, body { width: 1200px; height: 880px; overflow: hidden; }
  body {
    background: var(--stage);
    font-family: "Arimo", Arial, sans-serif;
    position: relative;
  }
  .card {
    position: absolute;
    left: 250px;
    width: 700px;
    height: 400px;
    border-radius: 28px;
    overflow: hidden;
  }
  .card--front { top: 30px; background: var(--green); }
  .card--back { top: 450px; background: var(--white); }

  .brand {
    position: absolute;
    display: flex;
    align-items: center;
    gap: 16px;
  }
  .brand__dot {
    width: 62px; height: 62px;
    border-radius: 50%;
    flex: none;
  }
  .brand__name {
    font-family: "Montserrat", sans-serif;
    font-weight: 700;
    font-size: 64px;
    line-height: 1;
    letter-spacing: -1px;
  }
  .brand__tagline {
    font-family: "Montserrat", sans-serif;
    font-weight: 500;
    font-size: 12px;
    letter-spacing: 4px;
    margin-top: 6px;
    padding-left: 4px;
  }

  .card--front .brand { left: 170px; top: 140px; color: var(--white); }
  .card--front .brand__dot { background: var(--white); }
  .front__web {
    position: absolute;
    left: 0; right: 0; top: 300px;
    text-align: center;
    color: var(--white);
    font-family: "Montserrat", sans-serif;
    font-weight: 500;
    font-size: 15px;
    letter-spacing: 4px;
  }

  .back__bands { position: absolute; inset: 0; }
  .card--back .brand { left: 48px; top: 78px; color: var(--ink-grey); }
  .card--back .brand__dot { background: var(--green); }
  .card--back .brand__name { font-size: 56px; }

  .person {
    position: absolute;
    left: 40px; top: 282px;
    color: var(--white);
    font-weight: 700;
    font-size: 19px;
    letter-spacing: 0.5px;
    text-transform: uppercase;
  }
  .person__role {
    font-weight: 400;
    margin-left: 8px;
    padding-left: 10px;
    border-left: 1.5px solid var(--white);
  }

  .contacts {
    position: absolute;
    left: 48px; top: 322px;
    list-style: none;
    color: var(--white);
    font-size: 15px;
  }
  .contacts li {
    display: flex;
    align-items: center;
    gap: 10px;
    height: 22px;
  }
  .contacts svg { width: 17px; height: 17px; flex: none; }

  .address {
    position: absolute;
    right: 40px; top: 258px;
    text-align: right;
    color: var(--white);
    font-size: 15px;
    line-height: 1.35;
  }
</style>
</head>
<body>

<section class="card card--front" aria-label="Card front">
  <div class="brand">
    <span class="brand__dot"></span>
    <div>
      <div class="brand__name">Plavex</div>
      <div class="brand__tagline">Technology Recruitment</div>
    </div>
  </div>
  <p class="front__web">www.plavex.co.uk</p>
</section>

<section class="card card--back" aria-label="Card back">
  <svg class="back__bands" viewBox="0 0 700 400" aria-hidden="true">
    <path d="M0,272 H252 Q272,272 272,252 V228 Q272,208 292,208 H700 V400 H0 Z" fill="var(--grey)"/>
    <path d="M0,310 H272 Q292,310 292,290 V266 Q292,246 312,246 H700 V400 H0 Z" fill="var(--green)"/>
  </svg>

  <div class="brand">
    <span class="brand__dot"></span>
    <div>
      <div class="brand__name">Plavex</div>
      <div class="brand__tagline">Technology Recruitment</div>
    </div>
  </div>

  <p class="person">Harriet Dunmore<span class="person__role">CEO</span></p>

  <ul class="contacts">
    <li>
      <svg viewBox="0 0 20 20" aria-hidden="true"><circle cx="10" cy="10" r="9" fill="none" stroke="#fff" stroke-width="1.4"/><rect x="7" y="5" width="6" height="10" rx="1" fill="none" stroke="#fff" stroke-width="1.3"/></svg>
      01632 960418
    </li>
    <li>
      <svg viewBox="0 0 20 20" aria-hidden="true"><circle cx="10" cy="10" r="9" fill="none" stroke="#fff" stroke-width="1.4"/><rect x="5" y="6.5" width="10" height="7" fill="none" stroke="#fff" stroke-width="1.3"/><path d="M5,6.5 L10,11 L15,6.5" fill="none" stroke="#fff" stroke-width="1.3"/></svg>
      Harriet@plavex.co.uk
    </li>
    <li>
      <svg viewBox="0 0 20 20" aria-hidden="true"><circle cx="10" cy="10" r="9" fill="none" stroke="#fff" stroke-width="1.4"/><circle cx="10" cy="10" r="5" fill="none" stroke="#fff" stroke-width="1.2"/><path d="M5,10 H15 M10,5 Q7,10 10,15 Q13,10 10,5" fill="none" stroke="#fff" stroke-width="1.1"/></svg>
      www.plavex.co.uk
    </li>
  </ul>

  <address class="address" style="font-style:normal">
    Brackwell House<br>
    Fenmoor Enterprise Park, Partridge Way<br>
    Norwich QB9 3KX
  </address>
</section>

</body>
</html>
```